Business card (AI file uploaded)

We need a business card design that is minimalist using existing logo (attached). Source files must be editable so we can make the same design with other names.

Screenshots included of a design I was working on to give you an idea of the style I would like. Looking for similar modern styles

Thanks

```html
<!DOCTYPE html>
<html lang="en">
<head>
<meta charset="utf-8">
<title>Calder Law Group – Business Card</title>
<link href="https://fonts.googleapis.com/css2?family=Exo+2:wght@300;400;600;700&display=swap" rel="stylesheet">
<style>
  :root {
    --page: #e8e6e2;
    --card-dark: #3a3a3c;
    --fold-deep: #939598;
    --fold-mid: #a0a2a5;
    --fold-light: #abadb0;
    --text-light: #ffffff;
    --text-muted: #9c9ea1;
    --card-w: 770px;
    --card-h: 440px;
  }
  * { box-sizing: border-box; margin: 0; padding: 0; }
  html, body {
    width: 1200px; height: 1020px; overflow: hidden;
    background: var(--page);
    font-family: "Exo 2", sans-serif;
  }
  .canvas {
    width: 1200px; height: 1020px;
    display: flex; flex-direction: column; align-items: center; justify-content: center;
    gap: 40px;
  }
  .card {
    position: relative;
    width: var(--card-w); height: var(--card-h);
    background: var(--card-dark);
    overflow: hidden;
    box-shadow: 0 6px 18px rgba(0,0,0,0.18);
  }
  .card__folds { position: absolute; inset: 0; width: 100%; height: 100%; }
  .brand {
    position: absolute; left: 58px; top: 96px;
    display: flex; align-items: center; gap: 22px;
    color: var(--text-light);
  }
  .brand__mark {
    width: 74px; height: 74px; border-radius: 50%;
    background: var(--text-light);
  }
  .brand__name {
    font-weight: 600; font-size: 50px; letter-spacing: 7px; line-height: 1;
  }
  .brand__sub {
    font-weight: 300; font-size: 22px; letter-spacing: 9px; margin-top: 4px;
  }
  .brand__suffix { font-size: 10px; letter-spacing: 1px; vertical-align: top; }
  .person {
    position: absolute; left: 156px; top: 212px; width: 290px;
    color: var(--text-light);
  }
  .person__role {
    font-weight: 400; font-size: 15px; letter-spacing: 3px; color: var(--text-muted);
  }
  .person__name {
    font-weight: 700; font-size: 30px; letter-spacing: 2px; line-height: 1.1;
    padding-bottom: 8px; border-bottom: 2px solid var(--text-light);
  }
  .contact { list-style: none; margin-top: 14px; }
  .contact__item {
    display: flex; align-items: center; gap: 12px;
    font-size: 15px; letter-spacing: 1px; line-height: 1; margin-bottom: 11px;
  }
  .contact__icon { width: 15px; height: 15px; flex: none; }
</style>
</head>
<body>
<main class="canvas">

  <section class="card card--front" aria-label="Business card front">
    <svg class="card__folds" viewBox="0 0 770 440" aria-hidden="true">
      <polygon points="470,0 770,0 770,440 470,440 405,220" fill="var(--fold-deep)"/>
      <polygon points="505,0 770,0 770,440 505,440 440,220" fill="var(--fold-mid)"/>
      <polygon points="540,0 770,0 770,440 540,440 475,220" fill="var(--fold-light)"/>
    </svg>

    <div class="brand">
      <span class="brand__mark"></span>
      <div>
        <div class="brand__name">CALDER</div>
        <div class="brand__sub">LAW GROUP <span class="brand__suffix">PC</span></div>
      </div>
    </div>

    <div class="person">
      <p class="person__role">GENERAL MANAGER</p>
      <h1 class="person__name">NATHANIEL REED</h1>
      <ul class="contact">
        <li class="contact__item">
          <svg class="contact__icon" viewBox="0 0 16 16"><path d="M4 1l3 3-2 2c1 2 3 4 5 5l2-2 3 3-2 3C7 15 1 9 1 3z" fill="#fff"/></svg>
          (555) 210 4478
        </li>
        <li class="contact__item">
          <svg class="contact__icon" viewBox="0 0 16 16"><rect x="1" y="3" width="14" height="10" fill="#fff"/><path d="M1 3l7 6 7-6" stroke="#3a3a3c" stroke-width="1.4" fill="none"/></svg>
          nreed@calder.com
        </li>
        <li class="contact__item">
          <svg class="contact__icon" viewBox="0 0 16 16" fill="none" stroke="#fff" stroke-width="1.4"><circle cx="8" cy="8" r="6.5"/><ellipse cx="8" cy="8" rx="2.8" ry="6.5"/><path d="M1.5 8h13"/></svg>
          www.calderlaw.com
        </li>
        <li class="contact__item">
          <svg class="contact__icon" viewBox="0 0 16 16"><path d="M8 1a5 5 0 0 1 5 5c0 4-5 9-5 9S3 10 3 6a5 5 0 0 1 5-5z" fill="#fff"/><circle cx="8" cy="6" r="2" fill="#3a3a3c"/></svg>
          48 BIRCH LANE, NY 10482
        </li>
      </ul>
    </div>
  </section>

  <section class="card card--back" aria-label="Business card back">
    <svg class="card__folds" viewBox="0 0 770 440" aria-hidden="true">
      <polygon points="150,0 770,0 770,440 150,440 85,220" fill="var(--fold-deep)"/>
      <polygon points="185,0 770,0 770,440 185,440 120,220" fill="var(--fold-mid)"/>
      <polygon points="220,0 770,0 770,440 220,440 155,220" fill="var(--fold-light)"/>
    </svg>
  </section>

</main>
</body>
</html>
```